Website redesign - vorelmik.com

We are looking to do a full redesign of vorelmik.com. Need a designer to come up overall layout and 3 specific pages and 3 different hero images.
Wireframes for the 3 pages are attached as well as site images. You don't have to follow the wireframes exactly, but instead the wireframe is there to show you the information that needs to be on each page. Feel free to rearrange as needed.
Our target market is self taught engineers. So definitely I want a more casual feel to it. I'm ok with fun bold colors as well. Really like websites that have the infinite scroll look/feel to them.
Looking to find a designer who will produce HTML and potentially even implement the HTML into our site checked in code.
HTML Code should be responsive/mobile first leveraging Bootstrap 4.
Attached files include:
0) Wireframe PDF
https://files.plomwerk.net/d/7Kx2pQmW9zLr4TbN8vYc3HsE5fJ/view?mode=share
1) Vorelmik Images zip 1
https://files.plomwerk.net/d/4Gt8nRvB2wQx6MkZ1pLd9YaC7hU/view?mode=share
2) Vorelmik Images zip 2
https://files.plomwerk.net/d/9Jw3sTcF5yNv1HqX8rKb2ZeM6dP/view?mode=share
Target Market(s)
I sell DIY Waterproof Electronics enclosures. Target audience is self taught DIY engineers
Coding
Coded - Design and coding required
Number of Pages Required
3 page
Colors
Designer to choose colors to be used in the design.
Look and feel

```html
<!DOCTYPE html>
<html lang="en">
<head>
<meta charset="utf-8">
<title>Vorelmik – Waterproof Project Boxes</title>
<link rel="stylesheet" href="https://fonts.googleapis.com/css2?family=Poppins:wght@400;500;600;700&display=swap">
<style>
:root{
  --blue:#1020f5;
  --red:#d4101e;
  --ink:#111111;
  --muted:#555a66;
  --wood:#b98a58;
  --wood-light:#d2a876;
  --wood-dark:#8e6238;
  --paper:#eef0f4;
  --steel:#7c8088;
  --plate:#1c1d21;
  --board:#3f8f4e;
  --soft:#f4f4f6;
  --white:#ffffff;
}
*{box-sizing:border-box;margin:0;padding:0}
html,body{width:1200px;height:3801px;overflow:hidden}
body{font-family:'Poppins',sans-serif;color:var(--ink);background:var(--white);position:relative}
.btn{display:inline-block;font-family:'Poppins',sans-serif;font-weight:500;font-size:14px;text-transform:uppercase;border-radius:6px;padding:0 24px;line-height:46px;color:var(--white);background:var(--blue);text-decoration:none}
.btn-white{background:var(--white);color:var(--ink)}
.btn-red{background:var(--red)}

/* Header */
.site-header{position:absolute;top:0;left:0;width:1200px;height:82px;background:var(--soft)}
.brand{position:absolute;left:112px;top:16px;font-size:40px;font-weight:600;color:var(--blue);letter-spacing:-0.5px;display:flex;align-items:center;gap:8px}
.brand-dot{width:12px;height:12px;border-radius:50%;background:#f4c20d}
.main-nav{position:absolute;left:360px;top:30px;display:flex;gap:15px;font-size:15px;font-weight:500;text-transform:uppercase}
.main-nav a{color:var(--ink);text-decoration:none}
.main-nav a.active{color:var(--blue);text-decoration:underline;text-underline-offset:4px}
.header-actions{position:absolute;left:862px;top:20px;display:flex;gap:12px}
.header-actions .btn{line-height:40px;font-size:14px;padding:0 22px}

/* Hero */
.hero{position:absolute;top:82px;left:0;width:1200px;height:513px;
  background:
    radial-gradient(ellipse 330px 210px at 290px 150px,rgba(238,240,244,.92),rgba(238,240,244,0) 75%),
    radial-gradient(ellipse 220px 120px at 960px 420px,rgba(150,170,190,.7),rgba(150,170,190,0) 75%),
    radial-gradient(ellipse 260px 150px at 480px 460px,rgba(176,140,104,.9),rgba(176,140,104,0) 75%),
    linear-gradient(120deg,var(--wood-light) 0%,var(--wood) 45%,#c49462 70%,var(--wood-dark) 100%)}
.hero-shade{position:absolute;inset:0;background:rgba(0,0,0,.08)}
.hero-title{position:absolute;top:154px;left:0;width:1200px;text-align:center;font-size:31px;font-weight:700;line-height:43px;color:var(--white);text-transform:uppercase;text-shadow:0 2px 5px rgba(0,0,0,.6)}
.hero .btn{position:absolute;left:526px;top:300px}
.hero-arrow{position:absolute;top:215px;width:30px;height:30px;border:2px solid rgba(255,255,255,.85);border-radius:50%}
.hero-arrow.left{left:58px}.hero-arrow.right{left:1104px}
.hero-arrow svg{width:26px;height:26px}

/* Videos */
.videos{position:absolute;top:595px;left:0;width:1200px;height:508px}
.section-title{font-size:30px;font-weight:600;text-transform:uppercase;line-height:1.3}
.videos .section-title{position:absolute;left:112px;top:115px}
.chev-list{position:absolute;left:112px;top:172px;list-style:none;font-size:16px;color:var(--muted);line-height:28px;width:300px}
.chev-list li{padding-left:22px;position:relative;margin-bottom:8px}
.chev-list li::before{content:"»";position:absolute;left:0;color:var(--red);font-weight:600}
.videos .btn{position:absolute;left:112px;top:312px}
.video-frame{position:absolute;left:527px;top:105px;width:562px;height:298px;background:var(--white);box-shadow:0 0 10px rgba(0,0,0,.15);padding:5px}
.video-frame .media{width:100%;height:100%;
  background:
    radial-gradient(ellipse 150px 120px at 430px 190px,rgba(20,20,22,.95),rgba(20,20,22,0) 80%),
    radial-gradient(ellipse 120px 60px at 260px 60px,rgba(80,150,90,.6),rgba(80,150,90,0) 80%),
    radial-gradient(ellipse 160px 130px at 230px 160px,rgba(40,40,46,.9),rgba(40,40,46,0) 80%),
    linear-gradient(90deg,#f2f2f4 0%,#e4e4e8 18%,#8d8f96 40%,#6b6d74 75%,#a9abb0 100%)}
.play{position:absolute;left:253px;top:121px;width:56px;height:56px;border-radius:50%;background:var(--white);display:flex;align-items:center;justify-content:center;box-shadow:0 0 0 6px rgba(255,255,255,.35)}

/* Blue band */
.band{position:absolute;top:1103px;left:0;width:1200px;height:339px;background:var(--blue)}
.band-track{position:absolute;left:65px;top:35px;width:580px;height:272px;background:linear-gradient(90deg,#2b2b2f,#3a3a3e 30%,#2b2b2f 70%,#38383c)}
.band-card{position:absolute;left:179px;top:17px;width:343px;height:307px;background:var(--white);display:flex;align-items:center;justify-content:center}
.band-card .media{width:210px;height:200px;background:radial-gradient(ellipse 105px 85px at 50% 52%,#d9d8d2 0%,#e9e8e3 60%,rgba(255,255,255,0) 100%)}
.band-arrow{position:absolute;top:175px}
.band-arrow.left{left:30px}.band-arrow.right{left:656px}
.band-text{position:absolute;left:746px;top:75px;color:var(--white);width:420px}
.band-text h2{font-size:31px;font-weight:600;text-transform:uppercase}
.band-text p{font-size:16px;line-height:28px;margin-top:14px}
.band-text .btn{margin-top:24px}

/* Makers */
.makers{position:absolute;top:1442px;left:0;width:1200px;height:563px;background:
  radial-gradient(ellipse 300px 160px at 140px 80px,rgba(236,238,242,.9),rgba(236,238,242,0) 80%),
  linear-gradient(135deg,#f2eee9,#e6dfd6 60%,#ddd3c6)}
.makers-heading{position:absolute;top:50px;left:0;width:1200px;text-align:center;font-size:31px;font-weight:600;line-height:46px;text-transform:uppercase}
.makers .section-title{position:absolute;left:112px;top:198px}
.ring-list{position:absolute;left:112px;top:258px;list-style:none;font-size:15.5px;color:var(--muted);line-height:37px;width:420px}
.ring-list li{padding-left:24px;position:relative}
.ring-list li::before{content:"";position:absolute;left:0;top:12px;width:11px;height:11px;border:1.5px solid var(--red);border-radius:50%}
.makers .btn{position:absolute;left:112px;top:455px}
.makers-photo{position:absolute;left:621px;top:186px;width:462px;height:322px;border-radius:10px;background:var(--red);padding:8px 0 0 8px}
.makers-photo .media{width:100%;height:100%;border-radius:8px;background:
  radial-gradient(ellipse 90px 70px at 340px 130px,rgba(150,156,166,.9),rgba(150,156,166,0) 80%),
  radial-gradient(ellipse 70px 55px at 130px 130px,rgba(40,60,70,.8),rgba(40,60,70,0) 80%),
  linear-gradient(135deg,#c9a47a,#b88e60 55%,#a57a4d)}

/* Testimonials */
.testimonials-title{position:absolute;top:2098px;left:0;width:1200px;text-align:center}
.quote-card{position:absolute;top:2187px;width:410px;height:216px;background:var(--white);box-shadow:0 0 8px rgba(0,0,0,.1);text-align:center;padding:14px 30px}
.quote-card.one{left:181px}.quote-card.two{left:609px}
.avatar{width:60px;height:60px;border-radius:50%;background:linear-gradient(#e4e6ea,#9aa2b3 60%,#2e3a5a);margin:0 auto 12px}
.quote-card p{font-size:15px;line-height:23px;color:var(--muted);position:relative}
.quote-card p::before{content:"\201C";position:absolute;left:-22px;top:-12px;font-size:70px;color:#c9ccd6;line-height:1}
.quote-card cite{display:block;text-align:right;font-style:normal;font-size:14px;font-weight:500;margin-top:14px;text-transform:uppercase}

/* Examples */
.examples-title{position:absolute;top:2496px;left:0;width:1200px;text-align:center}
.example{position:absolute;width:301px}
.example .media{width:301px;height:262px;box-shadow:0 0 6px rgba(0,0,0,.15);background-color:#fff}
.example span{display:block;font-size:15px;line-height:23px;margin-top:20px}
.c1{left:112px}.c2{left:449px}.c3{left:787px}
.r1{top:2593px}.r2{top:2944px}.r3{top:3295px}
.p1{background:radial-gradient(ellipse 120px 45px at 48% 38%,rgba(60,150,80,.85),rgba(60,150,80,0) 80%),radial-gradient(ellipse 140px 70px at 50% 62%,rgba(30,31,35,.9),rgba(30,31,35,0) 85%)}
.p2{background:radial-gradient(ellipse 110px 45px at 55% 30%,rgba(70,150,85,.85),rgba(70,150,85,0) 80%),radial-gradient(ellipse 130px 80px at 48% 60%,rgba(28,29,33,.95),rgba(28,29,33,0) 85%)}
.p3{background:radial-gradient(ellipse 90px 45px at 55% 35%,rgba(40,40,44,.9),rgba(40,40,44,0) 80%),radial-gradient(ellipse 130px 50px at 50% 65%,rgba(30,31,35,.85),rgba(30,31,35,0) 85%)}
.p4{background:radial-gradient(ellipse 110px 40px at 55% 25%,rgba(170,174,180,.95),rgba(170,174,180,0) 85%),radial-gradient(ellipse 130px 80px at 45% 62%,rgba(28,29,33,.95),rgba(28,29,33,0) 85%)}
.p5{background:radial-gradient(ellipse 80px 40px at 55% 28%,rgba(170,174,180,.95),rgba(170,174,180,0) 85%),radial-gradient(ellipse 110px 70px at 55% 62%,rgba(28,29,33,.9),rgba(28,29,33,0) 85%)}
.p6{background:radial-gradient(ellipse 130px 30px at 50% 38%,rgba(160,164,170,.95),rgba(160,164,170,0) 85%),radial-gradient(ellipse 130px 35px at 50% 55%,rgba(30,31,35,.85),rgba(30,31,35,0) 85%)}
.p7{background:radial-gradient(ellipse 60px 40px at 60% 40%,rgba(60,150,80,.85),rgba(60,150,80,0) 80%),radial-gradient(ellipse 140px 70px at 45% 48%,rgba(28,29,33,.95),rgba(28,29,33,0) 85%)}
.p8{background:radial-gradient(ellipse 70px 45px at 65% 45%,rgba(50,130,75,.9),rgba(50,130,75,0) 80%),radial-gradient(ellipse 70px 45px at 30% 35%,rgba(170,174,180,.95),rgba(170,174,180,0) 85%),radial-gradient(ellipse 140px 80px at 50% 55%,rgba(28,29,33,.95),rgba(28,29,33,0) 85%)}
.p9{background:radial-gradient(ellipse 80px 40px at 60% 30%,rgba(60,150,80,.85),rgba(60,150,80,0) 80%),radial-gradient(ellipse 140px 85px at 50% 55%,rgba(28,29,33,.95),rgba(28,29,33,0) 85%)}

/* Footer */
.site-footer{position:absolute;top:3726px;left:0;width:1200px;height:75px;background:var(--soft);font-size:15px}
.site-footer .copy{position:absolute;left:112px;top:26px}
.site-footer .follow{position:absolute;left:958px;top:26px;display:flex;align-items:center;gap:10px}
.social{width:12px;height:12px;border-radius:2px;background:var(--ink)}
</style>
</head>
<body>

<header class="site-header">
  <div class="brand">Vorelmik<span class="brand-dot"></span></div>
  <nav class="main-nav">
    <a class="active" href="#">Home</a><a href="#">Enclosures</a><a href="#">Designs</a><a href="#">FAQs</a><a href="#">Videos</a><a href="#">Contact Us</a>
  </nav>
  <div class="header-actions">
    <a class="btn" href="#">Sign In</a><a class="btn btn-red" href="#">Sign Up</a>
  </div>
</header>

<section class="hero" role="img" aria-label="Project box build kit laid out on a wooden workbench with instructions, panels, screws and tools">
  <div class="hero-shade"></div>
  <h1 class="hero-title">Waterproof project boxes<br>customized to your exact<br>needs.</h1>
  <a class="btn" href="#">Get Started</a>
  <span class="hero-arrow left"><svg viewBox="0 0 26 26"><path d="M14 8l-5 5 5 5M19 8l-5 5 5 5" fill="none" stroke="#fff" stroke-width="2"/></svg></span>
  <span class="hero-arrow right"><svg viewBox="0 0 26 26"><path d="M7 8l5 5-5 5M12 8l5 5-5 5" fill="none" stroke="#fff" stroke-width="2"/></svg></span>
</section>

<section class="videos">
  <h2 class="section-title">Vorelmik Videos</h2>
  <ul class="chev-list">
    <li>Customize your Project Box using our Designer</li>
    <li>Customize your Project Box using our Designer</li>
  </ul>
  <a class="btn" href="#">Get Started</a>
  <div class="video-frame">
    <div class="media" role="img" aria-label="Video still of an assembled enclosure with cables and electronics"></div>
    <div class="play"><svg width="32" height="32" viewBox="0 0 32 32"><circle cx="16" cy="16" r="13" fill="none" stroke="#d4101e" stroke-width="2.5"/><path d="M13 10l9 6-9 6z" fill="#d4101e"/></svg></div>
  </div>
</section>

<section class="band">
  <div class="band-track"></div>
  <div class="band-card"><div class="media" role="img" aria-label="Grey hinged waterproof enclosure"></div></div>
  <svg class="band-arrow left" width="14" height="24" viewBox="0 0 14 24"><path d="M12 2L2 12l10 10" fill="none" stroke="#fff" stroke-width="2"/></svg>
  <svg class="band-arrow right" width="14" height="24" viewBox="0 0 14 24"><path d="M2 2l10 10L2 22" fill="none" stroke="#fff" stroke-width="2"/></svg>
  <div class="band-text">
    <h2>Water Proof Project</h2>
    <p>Mounting Kits for all the popular water proof project boxes with many sizes to choose from</p>
    <a class="btn btn-white" href="#">Get Started</a>
  </div>
</section>

<section class="makers">
  <h2 class="makers-heading">Vorelmik waterproof project boxes were built<br>by makers for makers</h2>
  <h3 class="section-title">Waterproof Project</h3>
  <ul class="ring-list">
    <li>Design to your specifications</li>
    <li>Maker components: Nodeboard, Berrycore Pi,<br>Voltwell Power</li>
    <li>Detailed build instructions, videos, walkthroughs</li>
    <li>DIY made to look professional</li>
  </ul>
  <a class="btn" href="#">Get Started</a>
  <div class="makers-photo"><div class="media" role="img" aria-label="Mounting plate with controller boards and power supply on a workbench"></div></div>
</section>

<h2 class="section-title testimonials-title">What our customers have to say</h2>
<div class="quote-card one">
  <div class="avatar" role="img" aria-label="Customer portrait"></div>
  <p>Great work at a reasonable cost.I can't them enough.If you're doing custom boxes forlight shows, this is where you go.</p>
  <cite>-Omar T</cite>
</div>
<div class="quote-card two">
  <div class="avatar" role="img" aria-label="Customer portrait"></div>
  <p>Fantastic service/product..whether you simply thedesign and do all of thefabrication yourself or simplyorder the kits.</p>
  <cite>-Kelso R.</cite>
</div>

<h2 class="section-title examples-title">See real examples from our customers</h2>
<div class="example c1 r1"><div class="media p1" role="img" aria-label="Customer controller build on stacked mounting plates"></div><span>KTR BX8-72 w/ P16v2 +<br>Expansion board</span></div>
<div class="example c2 r1"><div class="media p2" role="img" aria-label="Customer controller build on mounting plate"></div><span>KTR BX8-72 w/ P16v2 +<br>Expansion board</span></div>
<div class="example c3 r1"><div class="media p3" role="img" aria-label="Customer relay board build on mounting plate"></div><span>KTR BX8-72 w/ P16v2 +<br>Expansion board</span></div>
<div class="example c1 r2"><div class="media p4" role="img" aria-label="Customer build with power supply on top plate"></div><span>KTR BX8-72 w/ P16v2 +<br>Expansion board</span></div>
<div class="example c2 r2"><div class="media p5" role="img" aria-label="Customer build with power supply"></div><span>KTR BX8-72 w/ P16v2 +<br>Expansion board</span></div>
<div class="example c3 r2"><div class="media p6" role="img" aria-label="Customer build with two power supplies"></div><span>KTR BX8-72 w/ P16v2 +<br>Expansion board</span></div>
<div class="example c1 r3"><div class="media p7" role="img" aria-label="Customer build with fan and boards"></div><span>KTR BX8-72 w/ P16v2 +<br>Expansion board</span></div>
<div class="example c2 r3"><div class="media p8" role="img" aria-label="Customer build with power supply and board"></div><span>KTR BX8-72 w/ P16v2 +<br>Expansion board</span></div>
<div class="example c3 r3"><div class="media p9" role="img" aria-label="Customer build with stacked boards"></div><span>KTR BX8-72 w/ P16v2 +<br>Expansion board</span></div>

<footer class="site-footer">
  <div class="copy">Copyright 2019-2020 @ vorelmik designer.</div>
  <div class="follow">Follow Us: <span class="social"></span><span class="social"></span></div>
</footer>

</body>
</html>
```